Boutique Store Selling Antiques and Unique Finds

I need a Web Page designed for my Store Called "Willow Lane". I would like a very classic, muted design that looks European when pulled up. I will be selling Antiques from all over the world and Unique finds that have reproduced. I will also be selling high-end purses and jewelry with unique, reasonable products for the every-day buyer as well.

Target Market(s)

25-70 year old men and women;)

Coding

Coded - Design and coding required

Number of Pages Required

1 page

Colors

Designer to choose only greyscale colors for use in the design.

Requirements
Must have
• I want it

```html
<!DOCTYPE html>
<html lang="en">
<head>
<meta charset="utf-8">
<title>Willow Lane — Antiques &amp; Unique Finds</title>
<link href="https://fonts.googleapis.com/css2?family=Raleway:wght@400;500;600;700&family=Montserrat:wght@700&display=swap" rel="stylesheet">
<style>
:root{
  --ink:#111;
  --muted:#555;
  --white:#fff;
  --tint:#e8f0f9;
  --aqua:#b5dde0;
  --sale:#d8232a;
  --gold:#e2b61e;
  --hero-a:#3b3028;
  --hero-b:#7a6a58;
  --footer:#000;
  --line:#333;
}
*{box-sizing:border-box;margin:0;padding:0}
html,body{width:1200px;height:2726px;overflow:hidden}
body{font-family:"Raleway",sans-serif;color:var(--ink);background:var(--white);position:relative}
.abs{position:absolute}

/* header */
.site-header{height:86px;position:relative;background:var(--white)}
.brand{left:113px;top:36px;font-size:17px;font-weight:600;letter-spacing:3px;text-transform:uppercase;color:var(--ink)}
.nav{top:44px;font-size:15px;font-weight:600;color:var(--ink)}
.header-icons{left:1020px;top:43px;display:flex;gap:10px}

/* hero */
.hero{top:86px;left:0;width:1200px;height:559px;background:radial-gradient(ellipse at 65% 55%,var(--hero-b),var(--hero-a) 70%)}
.hero-title{left:112px;top:266px;font-size:51px;font-weight:700;color:var(--white);letter-spacing:.5px}
.hero-text{left:113px;top:334px;width:440px;font-size:15px;line-height:24px;color:var(--white)}
.btn-learn{left:112px;top:401px;width:175px;height:52px;border-radius:26px;background:var(--aqua);font-size:15px;font-weight:600;color:var(--ink);display:flex;align-items:center;justify-content:center}

/* featured */
.featured{top:645px;left:0;width:1200px;height:876px;background:var(--tint)}
.section-title{width:1200px;text-align:center;font-size:36px;font-weight:600}
.featured-intro{left:270px;top:153px;width:630px;text-align:center;font-size:15px;line-height:24px;color:#333}
.product-card{top:271px;width:250px;height:441px;background:var(--white);box-shadow:0 1px 4px rgba(0,0,0,.12);text-align:center}
.product-photo{position:absolute;left:20px;top:18px;width:210px;height:210px;border-radius:6px}
.product-name{position:absolute;top:256px;width:100%;font-size:16px;font-weight:600}
.stars{position:absolute;top:288px;left:0;width:100%;display:flex;justify-content:center;gap:2px}
.price{position:absolute;top:318px;width:100%;font-size:15px;font-weight:700;color:var(--sale)}
.btn-cart{position:absolute;left:53px;top:359px;width:146px;height:43px;border:1px solid var(--ink);border-radius:3px;font-size:13px;font-weight:600;display:flex;align-items:center;justify-content:center}
.sale-badge{position:absolute;left:15px;top:6px;width:56px;height:56px;border-radius:50%;background:var(--sale);color:var(--white);font-size:14px;font-weight:700;display:flex;align-items:center;justify-content:center}
.dots{top:762px;left:565px;display:flex;gap:5px}
.dot{width:14px;height:14px;border-radius:50%;border:2px solid #444}
.dot.active{background:#444}

/* arrivals */
.arrivals-title{top:1600px;font-family:"Montserrat",sans-serif;font-weight:700;font-size:35px}
.arrival-card{top:1687px;width:467px;height:535px;background:var(--white);box-shadow:0 1px 5px rgba(0,0,0,.15);text-align:center}
.arrival-photo{position:absolute;left:6px;top:6px;width:455px;height:430px;border-radius:8px}
.arrival-name{position:absolute;top:462px;width:100%;font-size:15px;color:var(--muted)}
.arrival-price{position:absolute;top:489px;width:100%;font-size:16px;color:#333}
.slider-arrow{width:46px;height:46px;border-radius:50%;background:var(--white);box-shadow:0 1px 4px rgba(0,0,0,.2);display:flex;align-items:center;justify-content:center;top:1931px}

/* footer */
.site-footer{top:2310px;left:0;width:1200px;height:416px;background:var(--footer);color:var(--white);text-align:center}
.news-title{top:44px;width:100%;font-size:34px;font-weight:700}
.news-sub{top:94px;width:100%;font-size:15px;font-weight:600}
.news-form{left:244px;top:150px;width:706px;height:54px;border-radius:27px;background:var(--white);overflow:hidden}
.news-input{position:absolute;left:25px;top:17px;font-size:16px;color:#777}
.news-btn{position:absolute;right:0;top:0;width:153px;height:54px;background:var(--aqua);color:var(--white);font-size:16px;font-weight:600;display:flex;align-items:center;justify-content:center}
.social{top:236px;left:0;width:100%;display:flex;justify-content:center;gap:26px;font-size:16px}
.social span{display:flex;align-items:center;gap:7px}
.social i{width:9px;height:9px;border-radius:50%;background:var(--white);display:inline-block}
.footer-rule{left:112px;top:310px;width:976px;height:1px;background:var(--line)}
.copyright{top:352px;width:100%;font-size:15px}
</style>
</head>
<body>
<svg width="0" height="0" style="position:absolute">
  <defs>
    <symbol id="star" viewBox="0 0 20 20"><polygon points="10,1 12.6,7 19,7.5 14,11.8 15.6,18.3 10,14.8 4.4,18.3 6,11.8 1,7.5 7.4,7" /></symbol>
  </defs>
</svg>

<header class="site-header">
  <div class="abs brand">Willow Lane</div>
  <nav>
    <span class="abs nav" style="left:378px">HOME</span>
    <span class="abs nav" style="left:468px">PRODUCT</span>
    <span class="abs nav" style="left:582px">SERVICE</span>
    <span class="abs nav" style="left:689px">BLOG</span>
    <span class="abs nav" style="left:775px">CONTACT US</span>
  </nav>
  <div class="abs header-icons">
    <svg width="15" height="15" viewBox="0 0 16 16"><circle cx="6.5" cy="6.5" r="4.5" fill="none" stroke="#111" stroke-width="2.2"/><line x1="10" y1="10" x2="14.5" y2="14.5" stroke="#111" stroke-width="2.4"/></svg>
    <svg width="15" height="15" viewBox="0 0 16 16"><path d="M5 5V3.5a3 3 0 0 1 6 0V5" fill="none" stroke="#111" stroke-width="1.6"/><rect x="2" y="5" width="12" height="10" fill="#111"/></svg>
    <svg width="15" height="15" viewBox="0 0 16 16"><circle cx="8" cy="5" r="3.3" fill="none" stroke="#111" stroke-width="1.4"/><path d="M2.5 15c0-4 2.5-5.5 5.5-5.5s5.5 1.5 5.5 5.5z" fill="none" stroke="#111" stroke-width="1.4"/></svg>
  </div>
</header>

<section class="abs hero" role="img" aria-label="Engraved antique metal elephant figurine among brass vessels on a patterned rug">
</section>
<h1 class="abs hero-title">WILLOW LANE</h1>
<p class="abs hero-text">Sed ut perspiciatis unde omnis iste natus error sit voluptatem accusantium doloremque laudantium, totam rem aperiam</p>
<div class="abs btn-learn">LEARN MORE</div>

<section class="abs featured">
  <h2 class="abs section-title" style="top:97px">Featured Products</h2>
  <p class="abs featured-intro">Sed ut perspiciatis unde omnis iste natus error sit voluptatem accusantium doloremque laudantium, totam rem aperiam, eaque ipsa quae</p>

  <div class="abs product-card" style="left:57px">
    <div class="product-photo" role="img" aria-label="Ornate antique silver key" style="background:radial-gradient(circle,#9a9a9a,#f4f4f4 60%)"></div>
    <div class="product-name">Sed ut perspiciatis</div>
    <div class="stars"><svg width="14" height="14" fill="var(--gold)"><use href="#star"/></svg><svg width="14" height="14" fill="var(--gold)"><use href="#star"/></svg><svg width="14" height="14" fill="var(--gold)"><use href="#star"/></svg><svg width="14" height="14" fill="var(--gold)"><use href="#star"/></svg><svg width="14" height="14" fill="none" stroke="var(--gold)"><use href="#star"/></svg></div>
    <div class="price">$20.00</div>
    <div class="btn-cart">ADD TO CART</div>
  </div>

  <div class="abs product-card" style="left:336px">
    <div class="product-photo" role="img" aria-label="Engraved golden oil lamp" style="background:radial-gradient(circle,#b88a2e,#fbf6ea 60%)"></div>
    <div class="product-name">Sed ut perspiciatis</div>
    <div class="stars"><svg width="14" height="14" fill="var(--gold)"><use href="#star"/></svg><svg width="14" height="14" fill="var(--gold)"><use href="#star"/></svg><svg width="14" height="14" fill="var(--gold)"><use href="#star"/></svg><svg width="14" height="14" fill="var(--gold)"><use href="#star"/></svg><svg width="14" height="14" fill="none" stroke="var(--gold)"><use href="#star"/></svg></div>
    <div class="price">$20.00</div>
    <div class="btn-cart">ADD TO CART</div>
  </div>

  <div class="abs product-card" style="left:615px">
    <div class="product-photo" role="img" aria-label="Open gold pocket watch with chain" style="background:radial-gradient(circle,#d6b56a,#fbf7ee 60%)"></div>
    <div class="sale-badge">Sale!</div>
    <div class="product-name">Sed ut perspiciatis</div>
    <div class="stars"><svg width="14" height="14" fill="var(--gold)"><use href="#star"/></svg><svg width="14" height="14" fill="var(--gold)"><use href="#star"/></svg><svg width="14" height="14" fill="var(--gold)"><use href="#star"/></svg><svg width="14" height="14" fill="var(--gold)"><use href="#star"/></svg><svg width="14" height="14" fill="none" stroke="var(--gold)"><use href="#star"/></svg></div>
    <div class="price">$20.00</div>
    <div class="btn-cart">ADD TO CART</div>
  </div>

  <div class="abs product-card" style="left:893px">
    <div class="product-photo" role="img" aria-label="Antique leather-bound book" style="background:linear-gradient(#fff 6%,#7a3f1c 8%,#8f4d24 92%,#fff 94%);left:53px;width:144px"></div>
    <div class="product-name">Sed ut perspiciatis</div>
    <div class="stars"><svg width="14" height="14" fill="var(--gold)"><use href="#star"/></svg><svg width="14" height="14" fill="var(--gold)"><use href="#star"/></svg><svg width="14" height="14" fill="var(--gold)"><use href="#star"/></svg><svg width="14" height="14" fill="var(--gold)"><use href="#star"/></svg><svg width="14" height="14" fill="none" stroke="var(--gold)"><use href="#star"/></svg></div>
    <div class="price">$20.00</div>
    <div class="btn-cart">ADD TO CART</div>
  </div>

  <div class="abs dots"><span class="dot active"></span><span class="dot"></span><span class="dot"></span><span class="dot"></span></div>
</section>

<h2 class="abs section-title arrivals-title">New Arrivals</h2>
<div class="abs slider-arrow" style="left:30px"><svg width="12" height="12" viewBox="0 0 12 12"><path d="M8 1 3 6l5 5" fill="none" stroke="#111" stroke-width="1.5"/></svg></div>
<div class="abs slider-arrow" style="left:1118px"><svg width="12" height="12" viewBox="0 0 12 12"><path d="M4 1l5 5-5 5" fill="none" stroke="#111" stroke-width="1.5"/></svg></div>

<div class="abs arrival-card" style="left:111px">
  <div class="arrival-photo" role="img" aria-label="Gilded star crown resting on a stack of old books" style="background:linear-gradient(#cfc6b8,#8b6a3a 55%,#5a3a22)"></div>
  <div class="arrival-name">Lorem ipsum dolor sit</div>
  <div class="arrival-price">£275.00</div>
</div>
<div class="abs arrival-card" style="left:617px">
  <div class="arrival-photo" role="img" aria-label="Jewelled antique bronze crown on a stand" style="background:linear-gradient(#d8cfc4,#7a6440 50%,#2f2f2f)"></div>
  <div class="arrival-name">Lorem ipsum dolor sit</div>
  <div class="arrival-price">£275.00</div>
</div>

<footer class="abs site-footer">
  <h2 class="abs news-title">Subscribe to our Newsletter</h2>
  <p class="abs news-sub">Sign up for free and be the first to get notified about new posts.</p>
  <div class="abs news-form">
    <span class="news-input">Your email address</span>
    <span class="news-btn">Subscribe</span>
  </div>
  <div class="abs social">
    <span><i></i>Friendbook</span>
    <span><i></i>Chirper</span>
    <span><i></i>Snapgram</span>
    <span><i></i>Viewtube</span>
  </div>
  <div class="abs footer-rule"></div>
  <p class="abs copyright">© Copyright 2021 Willow Lane All rights reserved.</p>
</footer>
</body>
</html>
```